KRT Project Signage

Need a sign to be displayed in the front of properties currently under Construction or Renovation to advertise our company information. Need it to be Professional and Contemporary. We are a Design/Build Construction Company. Information should include Company Name, email, website, phone number. Attached: Logo and company brochure, also included and inspiration images

```html
<!DOCTYPE html>
<html lang="en">
<head>
<meta charset="utf-8">
<title>KRT Construction – Project Sign</title>
<link rel="stylesheet" href="https://fonts.googleapis.com/css2?family=Montserrat:wght@500;600;700&display=swap">
<style>
  :root {
    --page: #2e2e2e;
    --sign-dark: #1f1f1f;
    --accent: #f2ea4a;
    --ink: #111111;
    --white: #ffffff;
  }
  * { box-sizing: border-box; margin: 0; padding: 0; }
  html, body {
    width: 1200px; height: 1200px; overflow: hidden;
    background: var(--page);
    font-family: "Montserrat", sans-serif;
  }
  .sign {
    position: absolute; left: 40px; top: 226px;
    width: 1120px; height: 748px;
    background: var(--sign-dark);
    overflow: hidden;
  }
  .brand-name {
    position: absolute; left: 126px; top: 236px;
    color: var(--white);
    font-weight: 600; font-size: 74px; letter-spacing: 2px;
    line-height: 1; white-space: nowrap;
  }
  .tagline {
    position: absolute; left: 125px; top: 342px;
    width: 431px; height: 68px;
    background: var(--accent);
    border-radius: 12px;
    display: flex; align-items: center; justify-content: center;
    color: var(--ink);
    font-weight: 500; font-size: 33px; letter-spacing: 1px;
  }
  .divider {
    position: absolute; left: 0; top: 561px;
    width: 100%; height: 4px; background: var(--white);
  }
  .contact-band {
    position: absolute; left: 0; top: 565px;
    width: 100%; height: 183px;
    background: var(--accent);
    color: var(--ink);
    padding: 18px 0 0 83px;
  }
  .contact-row {
    display: flex; align-items: center; gap: 10px;
    white-space: nowrap; line-height: 1;
  }
  .contact-row svg { flex: none; }
  .row-address { height: 46px; font-weight: 500; font-size: 30px; }
  .row-phone { height: 64px; font-weight: 600; font-size: 40px; letter-spacing: -0.5px; }
  .row-phone .number { font-weight: 700; }
  .row-web { height: 46px; font-weight: 500; font-size: 29px; }
  .sep { margin: 0 4px; font-weight: 500; }
</style>
</head>
<body>
  <div class="sign">
    <div class="brand-name">KRT CONSTRUCTION</div>
    <div class="tagline">LUXURY RENOVATIONS</div>
    <div class="divider"></div>

    <div class="contact-band">
      <div class="contact-row row-address">
        <svg width="30" height="38" viewBox="0 0 32 40" aria-hidden="true">
          <path d="M16 2a10 10 0 0 0-10 10c0 8 10 18 10 18s10-10 10-18A10 10 0 0 0 16 2z" fill="var(--ink)"/>
          <circle cx="16" cy="12" r="4" fill="var(--accent)"/>
          <ellipse cx="16" cy="34" rx="14" ry="4" fill="none" stroke="var(--ink)" stroke-width="2"/>
        </svg>
        <span>1450 HARBOR VIEW RD., STE. 310 • CORAL BAY, FL 33400</span>
      </div>

      <div class="contact-row row-phone">
        <svg width="30" height="36" viewBox="0 0 32 38" aria-hidden="true">
          <path d="M6 4c3-2 5 0 6 3l2 5c1 2-1 4-3 5 1 4 4 8 7 10 2-1 4-2 5-1l4 4c2 2 1 4-1 5-3 2-7 1-11-3C8 26 3 16 4 9c0-2 1-4 2-5z" fill="var(--ink)"/>
          <path d="M20 6a9 9 0 0 1 7 8M20 11a4 4 0 0 1 3 4" fill="none" stroke="var(--ink)" stroke-width="2"/>
        </svg>
        <span>DIRECT <span class="number">555.010.2846</span><span class="sep">|</span>OFFICE <span class="number">555.010.7730</span></span>
      </div>

      <div class="contact-row row-web">
        <svg width="30" height="28" viewBox="0 0 32 30" aria-hidden="true">
          <rect x="2" y="10" width="28" height="18" fill="var(--ink)"/>
          <path d="M2 10l14 10 14-10" fill="none" stroke="var(--accent)" stroke-width="2"/>
          <rect x="8" y="2" width="16" height="12" fill="var(--accent)" stroke="var(--ink)" stroke-width="2"/>
          <path d="M11 6h10M11 9h8" stroke="var(--ink)" stroke-width="1.5"/>
        </svg>
        <span>marc@krtconstruction.com</span>
        <span class="sep">|</span>
        <svg width="28" height="28" viewBox="0 0 30 30" aria-hidden="true">
          <circle cx="14" cy="14" r="12" fill="none" stroke="var(--ink)" stroke-width="2"/>
          <ellipse cx="14" cy="14" rx="5" ry="12" fill="none" stroke="var(--ink)" stroke-width="1.5"/>
          <path d="M2 14h24M4 8h20M4 20h20" stroke="var(--ink)" stroke-width="1.5"/>
          <path d="M18 17l10 4-4 1 3 4-2 1-3-4-2 3z" fill="var(--ink)"/>
        </svg>
        <span>www.krtconstruction.com</span>
      </div>
    </div>
  </div>
</body>
</html>
```